Professional Website

We are looking for a new website for our Staffing Company. Attached is a document with all the details and pages needed along with some examples of others websites.

We want a professional Look and feel around the same color theme as the attached Amber Compass.

We currently host our site on PageLoom.io. If the winning designer can also add to PageLoom, that is a plus.

```html
<!DOCTYPE html>
<html lang="en">
<head>
<meta charset="utf-8">
<title>HireWay Inc — Clerical &amp; Industrial Staffing</title>
<link href="https://fonts.googleapis.com/css2?family=Montserrat:wght@300;400;500;600;800&family=Roboto:wght@400&display=swap" rel="stylesheet">
<style>
  :root{
    --brand:#1b35aa;
    --brand-light:#3d57c9;
    --ink:#1c1c1c;
    --body:#3a3a3a;
    --paper:#ffffff;
    --mist:#f2f2f7;
    --footer:#232323;
    --footer-line:#4a4a4a;
  }
  *{margin:0;padding:0;box-sizing:border-box}
  html,body{width:993px;height:1200px;overflow:hidden}
  body{position:relative;font-family:'Montserrat',sans-serif;color:var(--ink);background:var(--paper)}
  .abs{position:absolute}

  /* header */
  .site-header{position:absolute;left:0;top:0;width:993px;height:64px;background:var(--paper)}
  .brand{left:20px;top:17px;font-size:22px;font-weight:800;color:var(--brand);letter-spacing:-0.5px}
  .nav a{position:absolute;top:25px;font-size:11px;font-weight:500;color:var(--ink);text-decoration:none}
  .nav a.active{color:var(--brand);border-bottom:1.5px solid var(--brand);padding-bottom:2px}
  .login{position:absolute;top:18px;height:28px;border:1px solid var(--brand);color:var(--brand);font-size:10.5px;font-weight:500;display:flex;align-items:center;justify-content:center;white-space:nowrap}
  .call-icon{left:842px;top:19px;width:25px;height:25px;border-radius:50%;background:var(--brand)}
  .call-label{left:874px;top:17px;font-size:10px;color:var(--brand)}
  .call-number{left:874px;top:30px;font-size:15px;font-weight:500;color:var(--brand)}

  /* hero */
  .hero{left:0;top:64px;width:993px;height:489px;background:linear-gradient(100deg,#aec5cc 0%,#c6d6da 35%,#9fb4bb 60%,#1e2a3c 80%,#151e2c 100%)}
  .hero-kicker{left:53px;top:170px;font-size:22px;font-weight:800;color:#fff}
  .hero-title{left:53px;top:200px;font-size:47px;font-weight:800;color:#fff;letter-spacing:0.5px}
  .btn{background:var(--brand);color:#fff;font-weight:800;display:flex;align-items:center;justify-content:center}
  .hero-btn{left:56px;top:272px;width:114px;height:38px;font-size:11.5px}

  /* choice band */
  .choice{top:553px;height:102px;color:#fff}
  .choice-job{left:0;width:496px;background:var(--brand)}
  .choice-hire{left:496px;width:497px;background:var(--brand-light)}
  .choice-circle{top:22px;width:56px;height:56px;border-radius:50%;background:#fff}
  .choice-text{top:39px;font-size:17px;font-weight:500}
  .choice-rule{top:26px;width:2px;height:45px;background:#fff}

  /* about */
  .about{left:0;top:655px;width:993px;height:377px;background:var(--mist)}
  .about-visual{left:0;top:0;width:496px;height:377px;background:radial-gradient(circle at 72% 25%,#e8d6cc 0%,#b89c95 18%,transparent 40%),linear-gradient(90deg,#4f6f96 0%,#7d94b4 35%,#5e6370 65%,#eceef4 100%)}
  .about-title{left:498px;top:37px;font-size:20px;font-weight:800;color:var(--ink)}
  .about-title span{color:var(--brand)}
  .about-rule{left:498px;top:72px;width:73px;height:2px;background:var(--brand)}
  .about-copy{left:498px;top:100px;width:371px;font-size:12px;font-weight:300;letter-spacing:0.45px;line-height:20px;color:var(--body);text-align:justify}
  .about-btn{left:500px;top:305px;width:92px;height:32px;font-size:10px}

  /* footer */
  .site-footer{left:0;top:1032px;width:993px;height:168px;background:var(--footer);color:#fff}
  .footer-brand{left:109px;top:28px;font-size:30px;font-weight:800;color:#fff;letter-spacing:-0.5px}
  .footer-divider{left:374px;top:29px;width:1px;height:52px;background:#bbb}
  .locations{left:406px;top:29px;font-size:11.5px;line-height:18.5px;font-weight:500}
  .footer-call{left:661px;top:33px;width:38px;height:38px;border-radius:50%;background:#fff}
  .footer-call-label{left:714px;top:25px;font-size:17px;font-weight:500}
  .footer-call-number{left:714px;top:47px;font-size:25px;font-weight:600}
  .footer-rule{left:108px;top:107px;width:773px;height:1px;background:var(--footer-line)}
  .copyright{left:0;top:131px;width:993px;text-align:center;font-family:'Roboto',sans-serif;font-size:10px}
</style>
</head>
<body>

<header class="site-header">
  <div class="abs brand">HireWay Inc</div>
  <nav class="nav">
    <a class="active" href="#" style="left:203px">Home</a>
    <a href="#" style="left:254px">job</a>
    <a href="#" style="left:289px">Employees</a>
    <a href="#" style="left:363px">Office Information</a>
  </nav>
  <a class="login" style="left:479px;width:100px">Employee Login</a>
  <a class="login" style="left:600px;width:114px">Zelvo Card Login</a>
  <a class="login" style="left:722px;width:103px">Orvel Bank Login</a>
  <svg class="abs call-icon" viewBox="0 0 25 25"><path d="M9 7.5c.6-.4 1.2-.3 1.5.3l1 1.8c.3.5.1 1-.3 1.3l-.7.5c.5 1.3 1.6 2.4 2.9 2.9l.5-.7c.3-.4.8-.6 1.3-.3l1.8 1c.6.3.7.9.3 1.5-.7 1-1.7 1.5-2.9 1.1-2.9-1-5.1-3.2-6.1-6.1-.4-1.2.1-2.2 1.1-2.9z" fill="#fff"/></svg>
  <div class="abs call-label">Call us</div>
  <div class="abs call-number">555-014-2290</div>
</header>

<section class="abs hero" role="img" aria-label="Businessman in a dark suit holding out an open hand with a glowing person icon surrounded by small figures"></section>
<div class="abs hero-kicker">WELCOME TO</div>
<div class="abs hero-title">HIREWAY INC</div>
<a class="abs btn hero-btn">READ MORE</a>

<section class="abs choice choice-job">
  <div class="abs choice-circle" style="left:108px"></div>
  <svg class="abs" style="left:119px;top:34px" width="34" height="32" viewBox="0 0 34 32" fill="none" stroke="#1b35aa" stroke-width="2.4"><rect x="2" y="8" width="30" height="21" rx="3"/><path d="M12 8V4h10v4M2 16h30"/><rect x="14" y="14" width="6" height="5"/></svg>
  <div class="abs choice-text" style="left:179px">I’m looking for a Job</div>
  <div class="abs choice-rule" style="left:411px"></div>
  <svg class="abs" style="left:440px;top:39px" width="28" height="24" viewBox="0 0 28 24" fill="none" stroke="#fff" stroke-width="2.4"><path d="M0 12h26M16 2l10 10-10 10"/></svg>
</section>

<section class="abs choice choice-hire">
  <div class="abs choice-circle" style="left:42px"></div>
  <svg class="abs" style="left:56px;top:32px" width="28" height="36" viewBox="0 0 28 36" fill="none" stroke="#3d57c9" stroke-width="2.2"><circle cx="14" cy="10" r="7"/><path d="M2 34v-6c0-5 4-8 8-8h8c4 0 8 3 8 8v6zM14 20v10"/></svg>
  <div class="abs choice-text" style="left:123px">I need Employees</div>
  <div class="abs choice-rule" style="left:329px"></div>
  <svg class="abs" style="left:355px;top:39px" width="28" height="24" viewBox="0 0 28 24" fill="none" stroke="#fff" stroke-width="2.4"><path d="M0 12h26M16 2l10 10-10 10"/></svg>
</section>

<section class="abs about">
  <div class="abs about-visual" role="img" aria-label="Profile of a man in glasses overlaid with a digital globe of connected people icons"></div>
  <h2 class="abs about-title"><span>ABOUT</span> HIREWAY INC</h2>
  <div class="abs about-rule"></div>
  <p class="abs about-copy">Greatest part of our daily job is that we are constantly bringing people together. Our Clients come to us in search of the perfect candidate and the job hunters approach us when they are in need of a job or looking for their next exciting role. Being able to work with and connect the two is incredibly satisfying. Not to mention that in today's current job market, employers are fighting for the top talent. This makes our employees and partners grateful for the help in finding it!</p>
  <a class="abs btn about-btn">READ MORE</a>
</section>

<footer class="abs site-footer">
  <div class="abs footer-brand">HireWay Inc</div>
  <div class="abs footer-divider"></div>
  <div class="abs locations">North Bend<br>Ashford<br>Millbrook</div>
  <svg class="abs footer-call" viewBox="0 0 38 38"><path d="M13.5 11c.9-.6 1.8-.4 2.3.5l1.5 2.7c.4.7.2 1.5-.5 2l-1 .7c.8 2 2.4 3.6 4.4 4.4l.7-1c.5-.7 1.3-.9 2-.5l2.7 1.5c.9.5 1.1 1.4.5 2.3-1 1.5-2.6 2.3-4.4 1.7-4.4-1.5-7.8-4.9-9.3-9.3-.6-1.8.2-3.4 1.700-4.4z" fill="#232323"/></svg>
  <div class="abs footer-call-label">Call us</div>
  <div class="abs footer-call-number">555-014-2290</div>
  <div class="abs footer-rule"></div>
  <div class="abs copyright">Copyright © 2022 All Rights Reserved</div>
</footer>

</body>
</html>
```